Roofing Contractor business card redesign

I want to redesign my business card with a fresh, eye catching concept

Target Market(s)

Residential Roofing Clients, potential employees, and subcontractors.

Industry/Entity Type

Business

Colors

Designer to choose colors to be used in the design.

Requirements
Nice to have
• I just want something that's more pleasing to the eye. You can use a combination of either / or of my logos.

```html
<!DOCTYPE html>
<html lang="en">
<head>
<meta charset="utf-8">
<title>Ridgeway General Contractors – Business Card</title>
<link rel="stylesheet" href="https://fonts.googleapis.com/css2?family=Roboto+Condensed:wght@400;700&family=Roboto:wght@400;500&display=swap">
<style>
  :root {
    --backdrop: #e8e3da;
    --card-white: #f7f6f4;
    --maroon: #4a1410;
    --maroon-deep: #3a0f0c;
    --orange: #e8731c;
    --ink: #3a2a24;
    --text-grey: #5a5a5a;
    --rule: #c9c6c2;
  }
  * { box-sizing: border-box; margin: 0; padding: 0; }
  html, body { width: 1200px; height: 911px; overflow: hidden; }
  body {
    background: var(--backdrop);
    display: flex;
    align-items: center;
    justify-content: center;
    gap: 40px;
  }
  .card {
    width: 540px;
    height: 309px;
    border-radius: 16px;
    box-shadow: 0 6px 18px rgba(0,0,0,.18);
    position: relative;
    overflow: hidden;
  }
  /* Front */
  .card-front { background: var(--card-white); }
  .contact-block {
    position: absolute;
    left: 38px;
    top: 40px;
    width: 230px;
    font-family: "Roboto", sans-serif;
    color: var(--text-grey);
  }
  .holder-name {
    font-family: "Roboto Condensed", sans-serif;
    font-weight: 700;
    font-size: 21px;
    color: var(--ink);
    letter-spacing: .3px;
  }
  .holder-role {
    font-size: 13px;
    color: var(--orange);
    line-height: 1.35;
  }
  .divider {
    border: 0;
    border-top: 1px dashed var(--rule);
    margin: 14px 0;
  }
  .address { font-size: 12.5px; line-height: 1.45; }
  .contact-list { list-style: none; font-size: 12px; line-height: 1.55; }
  .contact-list li { display: flex; align-items: center; gap: 8px; }
  .contact-list svg { width: 11px; height: 11px; fill: var(--ink); flex: none; }
  .crew-artwork {
    position: absolute;
    right: 34px;
    top: 34px;
    width: 240px;
    height: 240px;
    border-radius: 50%;
    background: radial-gradient(circle at 50% 45%, #f0a24e 0%, #e8731c 30%, #8a4a2a 62%, #3a1a14 100%);
    border: 6px solid var(--card-white);
    box-shadow: 0 0 0 3px var(--maroon-deep);
  }
  /* Back */
  .card-back {
    background: linear-gradient(160deg, #52170f 0%, var(--maroon) 55%, var(--maroon-deep) 100%);
    color: #fff;
    display: flex;
    flex-direction: column;
    align-items: center;
    justify-content: center;
  }
  .brand-name {
    display: flex;
    align-items: center;
    gap: 12px;
    font-family: "Roboto Condensed", sans-serif;
    font-weight: 700;
    font-size: 52px;
    line-height: 1;
    color: #fff;
  }
  .brand-dot {
    width: 40px;
    height: 40px;
    border-radius: 50%;
    background: var(--orange);
  }
  .brand-tagline {
    font-family: "Roboto Condensed", sans-serif;
    font-weight: 700;
    font-size: 22px;
    margin-top: 8px;
  }
  .brand-web {
    position: absolute;
    bottom: 30px;
    font-family: "Roboto", sans-serif;
    font-size: 11px;
    letter-spacing: 6px;
    color: #e9d9d4;
  }
</style>
</head>
<body>
  <section class="card card-front">
    <div class="contact-block">
      <h1 class="holder-name">SAM HOLLIS</h1>
      <p class="holder-role">Keystone Certified Roof Inspector<br>Licensed Property Adjuster</p>
      <hr class="divider">
      <p class="address">4810 Cedar Lane Suite 110<br>Fairview, TX 75069</p>
      <hr class="divider">
      <ul class="contact-list">
        <li><svg viewBox="0 0 24 24"><path d="M6.6 10.8a15.1 15.1 0 0 0 6.6 6.6l2.2-2.2a1 1 0 0 1 1-.25 11.4 11.4 0 0 0 3.6.57 1 1 0 0 1 1 1V20a1 1 0 0 1-1 1A17 17 0 0 1 3 4a1 1 0 0 1 1-1h3.5a1 1 0 0 1 1 1c0 1.25.2 2.45.57 3.57a1 1 0 0 1-.25 1z"/></svg>(555) 214-3300</li>
        <li><svg viewBox="0 0 24 24"><path d="M3 3h18v18H3z M5 5v14h14V5z" fill-rule="evenodd"/></svg>(555) 214-7781</li>
        <li><svg viewBox="0 0 24 24"><path d="M2 5h20v14H2z M4 7l8 6 8-6" /></svg>sam@ridgewaytx.com</li>
        <li><svg viewBox="0 0 24 24"><circle cx="12" cy="12" r="10"/></svg>www.ridgewaytx.com</li>
      </ul>
    </div>
    <div class="crew-artwork" role="img" aria-label="Circular illustration of a roofing crew with tools"></div>
  </section>

  <section class="card card-back">
    <div class="brand-name"><span>Ridgeway</span><span class="brand-dot"></span></div>
    <p class="brand-tagline">General Contractors, Inc.</p>
    <p class="brand-web">www.ridgewaytx.com</p>
  </section>
</body>
</html>
```